Website for International Non-Profit for Birth Parent Searching

LumaKin is a 501(c)(3) non-profit organization that helps Chinese adoptees search and reunite with birth families who were separated due the One Child Policy in China. We want to create a website that can link to an information database that allows website users to easily access information around search ads in an organized way; help connect families to professional searchers; provide resources for community support for adoptees and their families as they embark on a personal and emotional journey of finding birth family through support groups on social media and consultation/education on the searching process; and provide the opportunity for the adoptive community to give back through donations and volunteer opportunities. The final design should foster a sense of community and be easy navigable to access the multiple resources we provide to help families search for each other. We would like to see designs with red/black/white color schemes that are gentle, inviting, and family friendly to viewers. We would like to see some design layouts with Chinese themes, if possible.

```html
<!DOCTYPE html>
<html lang="en">
<head>
<meta charset="utf-8">
<title>LumaKin — Reuniting Adoptees and Birth Families</title>
<link href="https://fonts.googleapis.com/css2?family=Lato:wght@400;700;900&family=Raleway:wght@600;700;800&display=swap" rel="stylesheet">
<style>
:root{
  --red:#c0163a;
  --red-deep:#a8102f;
  --ink:#111111;
  --text:#333333;
  --muted:#6e6e6e;
  --line:#cfcfcf;
  --white:#ffffff;
  --black:#000000;
}
*{box-sizing:border-box;margin:0;padding:0}
html,body{width:1200px;height:4029px;overflow:hidden;background:var(--white)}
body{position:relative;font-family:'Lato',sans-serif;color:var(--text)}
.abs{position:absolute}
.brand{font-family:'Lato',sans-serif;font-weight:700;color:var(--red);font-size:35px;letter-spacing:0.5px}

/* header */
.site-header .brand{left:85px;top:24px}
.contact-item{display:flex;align-items:center;gap:16px;top:26px}
.contact-item .dot{width:38px;height:38px;border-radius:50%;background:var(--red);display:flex;align-items:center;justify-content:center}
.contact-item small{display:block;color:var(--red);font-size:14px}
.contact-item span{display:block;color:var(--ink);font-size:15px;margin-top:3px}
.header-rule{left:85px;width:1030px;top:91px;height:1px;background:var(--line)}
.main-nav{left:85px;width:1030px;top:117px;display:flex;justify-content:space-around;padding:0 40px}
.main-nav a,.footer-nav a{font-weight:700;font-size:15px;color:var(--ink);text-decoration:none;letter-spacing:0.2px}

/* hero */
.hero{left:0;top:158px;width:1200px;height:670px;background:linear-gradient(100deg,#8a8a70 0%,#6f7458 35%,#5d5440 60%,#3d3a2e 100%)}
.hero-shade{position:absolute;inset:0;background:rgba(0,0,0,0.18)}
.hero h1{position:absolute;left:0;width:1200px;top:222px;text-align:center;font-family:'Raleway',sans-serif;font-weight:700;font-size:51px;color:var(--white)}
.hero p{position:absolute;left:330px;width:540px;top:304px;text-align:center;color:var(--white);font-size:15px;line-height:26px}
.btn-red{background:var(--red);color:var(--white);font-weight:900;font-size:16px;display:flex;align-items:center;justify-content:center;letter-spacing:0.3px}
.hero .btn-red{position:absolute;left:521px;top:393px;width:156px;height:43px}
.hero .arrow{position:absolute;top:320px}

/* section heading */
.section-title{left:0;width:1200px;text-align:center;font-family:'Raleway',sans-serif;font-weight:700;font-size:38px;color:var(--ink);letter-spacing:1px}
.title-rule{width:82px;height:3px;background:var(--red)}

/* organized way */
.feature{width:300px;text-align:center;font-size:15px;line-height:26px;color:var(--ink);letter-spacing:0.2px}
.feature-icon{width:130px;height:130px;border-radius:18px;background:#f7e3e8;border:2px solid #e8b7c3;margin:0 auto 14px}

/* about */
.about-photo{left:0;top:1397px;width:600px;height:476px;background:linear-gradient(180deg,#e4e2df 0%,#d8d2cc 55%,#9a8e80 100%)}
.about-panel{left:600px;top:1397px;width:600px;height:476px;background:linear-gradient(135deg,#c6274a 0%,var(--red) 55%,#b51236 100%)}
.about-panel h2{position:absolute;left:84px;top:60px;font-family:'Raleway',sans-serif;font-weight:700;font-size:38px;color:var(--white);letter-spacing:1px}
.about-panel .rule{position:absolute;left:84px;top:124px;width:82px;height:3px;background:var(--white)}
.about-panel p{position:absolute;left:84px;top:160px;width:440px;font-size:15px;line-height:26px;color:var(--white)}
.btn-outline{position:absolute;left:84px;top:358px;width:158px;height:51px;border:1px solid var(--white);color:var(--white);font-weight:700;font-size:17px;display:flex;align-items:center;justify-content:center}

/* help cards */
.card{top:2079px;width:325px;height:365px;background:var(--white);box-shadow:0 2px 10px rgba(0,0,0,0.14)}
.card-photo{height:167px}
.card h3{margin:28px 24px 0;font-size:15px;font-weight:900;color:var(--ink);letter-spacing:0.4px}
.card p{margin:14px 24px 0;font-size:15px;line-height:24px;color:var(--muted);letter-spacing:0.3px}
.card a{display:flex;align-items:center;gap:8px;margin:16px 24px 0;color:var(--red);font-weight:900;font-size:15px;text-decoration:none}

/* testimonial */
.testimonial{left:0;top:2530px;width:1200px;height:497px;background:linear-gradient(120deg,#c8294b 0%,var(--red) 50%,#c0203f 100%)}
.testimonial h2{position:absolute;left:0;width:1200px;top:62px;text-align:center;font-family:'Raleway',sans-serif;font-weight:700;font-size:38px;color:var(--white);letter-spacing:1px}
.testimonial .rule{position:absolute;left:559px;top:121px;width:82px;height:3px;background:var(--white)}
.testimonial p{position:absolute;left:180px;width:840px;top:190px;text-align:center;color:var(--white);font-size:16px;line-height:26px;letter-spacing:0.2px}
.avatar{position:absolute;left:476px;top:316px;width:112px;height:112px;border-radius:50%;border:4px solid var(--white);background:linear-gradient(180deg,#d9dce0,#7b8088)}
.stars{position:absolute;left:622px;top:342px;display:flex;gap:6px}
.reviewer{position:absolute;left:623px;top:381px;color:var(--white);font-weight:900;font-style:italic;font-size:16px}

/* contact form */
.field{border:1px solid #8d8d8d;background:var(--white);font-size:15px;color:var(--text);padding:0 14px;display:flex;align-items:center;letter-spacing:0.3px}
.field.message{align-items:flex-start;padding-top:14px}
.contact-form .btn-red{position:absolute;left:499px;top:3520px;width:203px;height:52px;font-size:17px}

/* footer */
.site-footer{left:0;top:3658px;width:1200px;height:371px;background:var(--black)}
.site-footer .brand{position:absolute;left:0;width:1200px;top:52px;text-align:center}
.footer-nav{position:absolute;left:130px;width:940px;top:134px;display:flex;justify-content:space-between}
.footer-nav a{color:var(--white)}
.socials{position:absolute;left:517px;top:199px;display:flex;gap:19px}
.socials span{width:36px;height:36px;border-radius:50%;background:var(--red)}
.footer-rule{position:absolute;left:85px;width:1030px;top:288px;height:1px;background:#444}
.copyright{position:absolute;left:0;width:1200px;top:318px;text-align:center;color:var(--white);font-size:15px}
</style>
</head>
<body>

<header class="site-header">
  <div class="abs brand">LUMAKIN</div>
  <div class="abs contact-item" style="left:704px">
    <div class="dot"><svg width="18" height="18" viewBox="0 0 24 24"><path fill="#fff" d="M6.6 10.8a15 15 0 0 0 6.6 6.6l2.2-2.2a1 1 0 0 1 1-.25 11.4 11.4 0 0 0 3.6.57 1 1 0 0 1 1 1V20a1 1 0 0 1-1 1A17 17 0 0 1 3 4a1 1 0 0 1 1-1h3.5a1 1 0 0 1 1 1c0 1.25.2 2.45.57 3.57a1 1 0 0 1-.25 1z"/></svg></div>
    <div><small>contact:</small><span>(555) 204 318</span></div>
  </div>
  <div class="abs contact-item" style="left:934px">
    <div class="dot"><svg width="16" height="18" viewBox="0 0 24 24"><path fill="#fff" d="M12 2a7 7 0 0 0-7 7c0 5.25 7 13 7 13s7-7.75 7-13a7 7 0 0 0-7-7zm0 9.5A2.5 2.5 0 1 1 12 6.5a2.5 2.5 0 0 1 0 5z"/></svg></div>
    <div><small>Email:</small><span>info@lumakin.org</span></div>
  </div>
  <div class="abs header-rule"></div>
  <nav class="abs main-nav">
    <a href="#">HOME</a><a href="#">ABOUT US</a><a href="#">HOW ITS WORK</a><a href="#">ORGANIZATION</a><a href="#">HOW CAN HELP</a><a href="#">CONTACT US</a>
  </nav>
</header>

<section class="abs hero" role="img" aria-label="Family of three walking and smiling outside their home">
  <div class="hero-shade"></div>
  <svg class="arrow" style="left:46px" width="16" height="26" viewBox="0 0 16 26"><path d="M13 3 3 13l10 10" stroke="#fff" stroke-width="3" fill="none"/></svg>
  <svg class="arrow" style="left:1138px" width="16" height="26" viewBox="0 0 16 26"><path d="M3 3l10 10L3 23" stroke="#fff" stroke-width="3" fill="none"/></svg>
  <h1>WELL COME TO LUMAKIN</h1>
  <p>Lorem ipsum dolor sit amet, consectetur adipiscing elit, sed do eiusmod tempor incididunt ut labore et dolore magna aliqua.</p>
  <div class="btn-red">GET STARTED</div>
</section>

<section class="organized">
  <h2 class="abs section-title" style="top:908px">ORGANIZED WAY</h2>
  <div class="abs title-rule" style="left:568px;top:971px"></div>
  <div class="abs feature" style="left:74px;top:1060px">
    <div class="feature-icon" role="img" aria-label="Line icon of a magnifying glass over a child's face"></div>
    <div style="margin-top:8px">help connect families to professional searchers</div>
  </div>
  <div class="abs feature" style="left:395px;top:1020px;width:430px">
    <div class="feature-icon" role="img" aria-label="Line icon of a child holding a heart"></div>
    <div style="margin-top:30px">provide resources for community support for adoptees and their families as they embark on a personal and emotional journey of finding birth family through support groups on social media and consultation/education on the searching process;</div>
  </div>
  <div class="abs feature" style="left:865px;top:1035px;width:265px">
    <div class="feature-icon" role="img" aria-label="Line icon of two children side by side"></div>
    <div style="margin-top:22px">provide the opportunity for the adoptive community to give back through donations and volunteer opportunities.</div>
  </div>
</section>

<section class="about">
  <div class="abs about-photo" role="img" aria-label="Parents and daughter laughing together on a sofa"></div>
  <div class="abs about-panel">
    <h2>ABOUT US</h2>
    <div class="rule"></div>
    <p>Lorem ipsum dolor sit amet, consectetur adipiscing elit, sed do eiusmod tempor incididunt ut labore et dolore magna aliqua. Ut enim ad minim veniam, quis nostrud exercitation ullamco laboris nisi ut aliquip ex ea commodo consequat. Duis aute irure dolor in reprehenderit in voluptate velit esse cillum dolore eu fugiat nulla pariatur.</p>
    <div class="btn-outline">LEARN MORE</div>
  </div>
</section>

<section class="help">
  <h2 class="abs section-title" style="top:1948px">HOW YOU CAN HELP</h2>
  <div class="abs title-rule" style="left:559px;top:2016px"></div>

  <article class="abs card" style="left:86px">
    <div class="card-photo" role="img" aria-label="Parents holding their baby at home" style="background:linear-gradient(135deg,#c9b8a4,#8d7a68)"></div>
    <h3>LOREM IPSUM DOLOR SIT AME</h3>
    <p>ed ut perspiciatis unde omnis iste natus error sit doloremque ntium, totam rem aperiam, eaque ipsa.quae</p>
    <a href="#">Read More <svg width="14" height="14" viewBox="0 0 14 14"><circle cx="7" cy="7" r="7" fill="#c0163a"/><path d="M5.5 4l3 3-3 3" stroke="#fff" stroke-width="1.8" fill="none"/></svg></a>
  </article>
  <article class="abs card" style="left:438px">
    <div class="card-photo" role="img" aria-label="Smiling family of four outdoors" style="background:linear-gradient(135deg,#8f9c5a,#6b5d4c)"></div>
    <h3>LOREM IPSUM DOLOR SIT AME</h3>
    <p>ed ut perspiciatis unde omnis iste natus error sit doloremque ntium, totam rem aperiam, eaque ipsa.quae</p>
    <a href="#">Read More <svg width="14" height="14" viewBox="0 0 14 14"><circle cx="7" cy="7" r="7" fill="#c0163a"/><path d="M5.5 4l3 3-3 3" stroke="#fff" stroke-width="1.8" fill="none"/></svg></a>
  </article>
  <article class="abs card" style="left:789px">
    <div class="card-photo" role="img" aria-label="Family sitting on the grass in a park" style="background:linear-gradient(135deg,#a9c46a,#7b9150)"></div>
    <h3>LOREM IPSUM DOLOR SIT AME</h3>
    <p>ed ut perspiciatis unde omnis iste natus error sit doloremque ntium, totam rem aperiam, eaque ipsa.quae</p>
    <a href="#">Read More <svg width="14" height="14" viewBox="0 0 14 14"><circle cx="7" cy="7" r="7" fill="#c0163a"/><path d="M5.5 4l3 3-3 3" stroke="#fff" stroke-width="1.8" fill="none"/></svg></a>
  </article>
</section>

<section class="abs testimonial">
  <h2>OUR TESTIMONIAL</h2>
  <div class="rule"></div>
  <p>Sed ut perspiciatis unde omnis iste natus error sit voluptatem accusantium doloremque laudantium, totam rem aperiam, eaque ipsa quae ab illo inventore veritatis et quasi architecto beatae vitae dicta sunt explicabo. Nemo enim ipsam voluptatem quia voluptas sit aspernatur aut odit aut fugit, sed quia consequuntur magni dolores eos qui ratione voluptatem sequi nesciunt.</p>
  <div class="avatar" role="img" aria-label="Portrait of the reviewer"></div>
  <div class="stars">
    <svg width="16" height="16" viewBox="0 0 24 24"><path fill="#ffd400" d="M12 2l3 7h7l-5.6 4.4L18.5 21 12 16.6 5.5 21l2.1-7.6L2 9h7z"/></svg>
    <svg width="16" height="16" viewBox="0 0 24 24"><path fill="#ffd400" d="M12 2l3 7h7l-5.6 4.4L18.5 21 12 16.6 5.5 21l2.1-7.6L2 9h7z"/></svg>
    <svg width="16" height="16" viewBox="0 0 24 24"><path fill="#ffd400" d="M12 2l3 7h7l-5.6 4.4L18.5 21 12 16.6 5.5 21l2.1-7.6L2 9h7z"/></svg>
    <svg width="16" height="16" viewBox="0 0 24 24"><path fill="#ffd400" d="M12 2l3 7h7l-5.6 4.4L18.5 21 12 16.6 5.5 21l2.1-7.6L2 9h7z"/></svg>
    <svg width="16" height="16" viewBox="0 0 24 24"><path fill="#ffd400" d="M12 2l3 7h7l-5.6 4.4L18.5 21 12 16.6 5.5 21l2.1-7.6L2 9h7z"/></svg>
  </div>
  <div class="reviewer">Mara Lind</div>
</section>

<section class="contact-form">
  <h2 class="abs section-title" style="top:3106px">CONTACT FORM</h2>
  <div class="abs title-rule" style="left:559px;top:3173px"></div>
  <div class="abs field" style="left:175px;top:3227px;width:412px;height:47px">Name:</div>
  <div class="abs field" style="left:613px;top:3227px;width:412px;height:47px">Email:</div>
  <div class="abs field" style="left:175px;top:3303px;width:412px;height:48px">Number:</div>
  <div class="abs field" style="left:613px;top:3303px;width:412px;height:48px">Address:</div>
  <div class="abs field message" style="left:175px;top:3379px;width:850px;height:99px">Message:</div>
  <div class="btn-red">SEND MESSAGE</div>
</section>

<footer class="abs site-footer">
  <div class="brand">LUMAKIN</div>
  <nav class="footer-nav">
    <a href="#">HOME</a><a href="#">ABOUT US</a><a href="#">HOW ITS WORK</a><a href="#">ORGANIZATION</a><a href="#">HOW CAN HELP</a><a href="#">CONTACT US</a>
  </nav>
  <div class="socials" aria-label="Social media links"><span></span><span></span><span></span><span></span></div>
  <div class="footer-rule"></div>
  <div class="copyright">© Copyright 2021 LumaKin.All right reserved.</div>
</footer>

</body>
</html>
```